Modern & Simple Essential Oils Label

Company Name: Meadowlark Essentials

What we sell: Aromatherapy products, pure therapeutic essential oils.

Design need:
We are looking for a creative and youthful design for the labels used on small essentials oils.

I have two sizes of bottles that I use for essential oils a 5ml bottle and a 15ml bottle. They are dark Amber color glass with black lids. I like the clear labels or mayble a dark brown background. With white or clear lettering with punch of color too! Each oil type is represented by different color. (lavender- purple, lemon - yellow). The label will be the same for all the oils in the two sizes with only a different oil name & coordinating color.
5ml label size should be: 1 " x 2.625"
15ml label size should be: 1.5" x 3.5"

I have some labels that I have had another designer start on, but they aren't quite what I want and missing that something (alot!).. I don't know what. Interest maybe? Lack of design? I dunno.. they are attached. Maybe it's the logo? I don't know! But its gotta change! When I cut out a proof and put a sample on the bottle as I look straight on at the label all I see is a big dot, no logo.. nothing interesting.
Updates

Project Deadline Extended
Reason: Hi! Id like to extend this deadline. Ive been unavailable for a few days due to an illness and Im so far behind! Im feeling MUCH better and looking forward to getting caught up and move with the project. Im not sure how this works, but I attached a list of the oils that we currently have available. And in the list is the idea for the color schemes for the oils. The basic idea is for it to have a wide array of colors, so using different shades of greens, yellows, oranges and so on. So that its like a rainbow. We are not set of that particular color for that particular oil. It was just a idea list of possible colors for oils. Thanks so much!

Target Market(s)

Metro & Modern people. Interested in healthy organic living, Mostly women (some men) 20-45 who are interested in holistic healing.

Industry/Entity Type

It Company

Requirements
Must have
• A reputable look. Clean, organic, crisp, zen or spa-like feel. Modern, youthful appealing label design. Approachable and interesting, not intimidating so that I don't turn away people who are new or not familiar with how to use essential oils.
Should not have
• do NOT want the look to be anywhere close to medicinal, witchy, crafty, hippie, mystical, overly earthy, magical, or voodoo. Do not want it to look like something out of a grandmothers medicine cabinet.

```html
<!DOCTYPE html>
<html lang="en">
<head>
<meta charset="utf-8">
<title>Meadowlark Essentials – Basil Label</title>
<link href="https://fonts.googleapis.com/css2?family=Arimo:wght@400;700&family=Open+Sans:ital,wght@0,300;0,700;1,700&display=swap" rel="stylesheet">
<style>
  :root {
    --leaf: #3aaa35;
    --leaf-soft: #52b84c;
    --paper: #efeeee;
    --ink: #8a8a8a;
    --ink-dark: #7a7a7a;
    --white: #ffffff;
    --cut-mark: #666666;
    --logo-tint: #e9efe8;
  }
  html, body {
    margin: 0;
    padding: 0;
    width: 1200px;
    height: 591px;
    overflow: hidden;
    background: var(--white);
  }
  .label {
    position: relative;
    width: 1200px;
    height: 591px;
    font-family: "Arimo", Arial, sans-serif;
  }
  .cut-mark {
    position: absolute;
    left: 600px;
    width: 1px;
    height: 23px;
    background: var(--cut-mark);
  }
  .cut-mark--top { top: 45px; }
  .cut-mark--bottom { top: 522px; }

  /* Back panel: information, set vertically */
  .info-panel {
    position: absolute;
    left: 75px;
    top: 68px;
    width: 525px;
    height: 454px;
    background: var(--paper);
    overflow: hidden;
  }
  .info-panel__content {
    position: absolute;
    left: 0;
    top: 0;
    width: 454px;
    height: 525px;
    transform-origin: 0 0;
    transform: translate(0, 454px) rotate(-90deg);
    color: var(--ink);
    font-size: 16px;
    line-height: 21px;
  }
  .facts-box {
    position: absolute;
    left: 14px;
    top: 15px;
    width: 416px;
    height: 159px;
    border: 2px solid var(--leaf);
    background: var(--paper);
  }
  .facts-box__title {
    margin: 14px 0 0 16px;
    font-size: 20px;
    font-weight: 700;
    color: var(--ink-dark);
    line-height: 24px;
  }
  .facts-box__list {
    margin: 0 0 0 16px;
    padding: 0;
    list-style: none;
    font-size: 16px;
    line-height: 21px;
  }
  .facts-box__grade {
    position: absolute;
    left: 0;
    right: 0;
    bottom: 0;
    height: 30px;
    background: var(--leaf);
    color: var(--white);
    font-size: 16px;
    line-height: 30px;
    padding-left: 16px;
  }
  .company-block,
  .usage-note,
  .caution-note {
    position: absolute;
    left: 16px;
    width: 430px;
    margin: 0;
  }
  .company-block { top: 190px; }
  .usage-note { top: 254px; }
  .caution-note { top: 342px; }
  .caution-note strong { font-weight: 700; }

  /* Front panel */
  .front-panel {
    position: absolute;
    left: 600px;
    top: 68px;
    width: 524px;
    height: 452px;
    background: var(--leaf);
    color: var(--white);
  }
  .oil-descriptor {
    position: absolute;
    left: 335px;
    top: 49px;
    margin: 0;
    font-family: "Open Sans", Arial, sans-serif;
    font-weight: 700;
    font-style: italic;
    font-size: 19px;
    line-height: 29px;
    text-transform: uppercase;
  }
  .oil-name-art {
    position: absolute;
    left: 30px;
    top: 175px;
    width: 410px;
    height: 150px;
  }
  .front-panel__divider {
    position: absolute;
    left: 0;
    right: 0;
    top: 358px;
    height: 3px;
    background: var(--white);
  }
  .volume {
    position: absolute;
    left: 18px;
    top: 363px;
    width: 30px;
    height: 89px;
    display: flex;
    align-items: center;
    justify-content: center;
  }
  .volume span {
    display: block;
    transform: rotate(-90deg);
    white-space: nowrap;
    font-family: "Open Sans", Arial, sans-serif;
    font-weight: 700;
    font-size: 22px;
  }
  .volume-rule {
    position: absolute;
    left: 57px;
    top: 361px;
    width: 3px;
    height: 91px;
    background: var(--white);
  }
  .brand-name {
    position: absolute;
    left: 80px;
    top: 386px;
    margin: 0;
    font-family: "Open Sans", Arial, sans-serif;
    font-weight: 300;
    font-size: 36px;
    line-height: 44px;
    color: var(--logo-tint);
    letter-spacing: 0.5px;
  }
</style>
</head>
<body>
<main class="label">
  <div class="cut-mark cut-mark--top"></div>
  <div class="cut-mark cut-mark--bottom"></div>

  <section class="info-panel">
    <div class="info-panel__content">
      <div class="facts-box">
        <p class="facts-box__title">Supplemental Facts</p>
        <ul class="facts-box__list">
          <li>Serving Size: 1 drop</li>
          <li>Servings Per Container: About 250</li>
          <li>Oil: Rosmarinus Officinalis</li>
        </ul>
        <div class="facts-box__grade">100% Pure Therapeutic Grade</div>
      </div>

      <p class="company-block">Meadowlark Essentials<br>P.O. Box 402, Brookfield, OR 97031</p>

      <p class="usage-note">For aromatic, topical use. 100% pure therapeutic-grade essential oil. Dilute with a carrier oil before using.</p>

      <p class="caution-note"><strong>CAUTION</strong>: For External Use Only. Not for Ingestion. Keep away from eyes and mucous membranes. May cause skin sensitivity. If pregnant consult physician before use. Keep out of reach of children. Keep away from flame.</p>
    </div>
  </section>

  <section class="front-panel">
    <p class="oil-descriptor">Ocimum<br>Basilicum<br>100% Pure<br>Essential Oil</p>

    <svg class="oil-name-art" role="img" aria-label="Hand-lettered oil name: Basil" viewBox="0 0 410 150">
      <rect x="0" y="0" width="410" height="150" rx="18" fill="var(--leaf-soft)"/>
    </svg>

    <div class="front-panel__divider"></div>
    <div class="volume"><span>15 ml</span></div>
    <div class="volume-rule"></div>
    <p class="brand-name">meadowlark essentials</p>
  </section>
</main>
</body>
</html>
```